We need letterhead, Business Cards, and envelops designed. We have attached a design of our logo and a sample of letterhead idea that was started but never perfected, it is only an idea for the letterhead if you can design something better we may love that also we are open to change.
We want a design that looks professional in style. we are a non profit trade association in the construction industry. the green color in the attached design represent green building, and we like that. also if you just want to enhance the letterhead sample that we attached that would be fine also.
Thanks and good luck
also the name that should show on the first business cards should be Morgan Feltwick, Director are web address is www.pvtrn.org

```html
<!DOCTYPE html>
<html lang="en">
<head>
<meta charset="utf-8">
<title>PVTRN Stationery Set</title>
<link href="https://fonts.googleapis.com/css2?family=Source+Sans+3:wght@400;600;700&display=swap" rel="stylesheet">
<style>
  :root {
    --backdrop: #d6d6d6;
    --paper: #ffffff;
    --slate: #7b7b7b;
    --slate-dark: #6a6a6a;
    --ink: #1c1c1c;
    --ink-soft: #3a3a3a;
    --rule: #6f6f6f;
    --green: #6fa23a;
  }
  * { box-sizing: border-box; margin: 0; padding: 0; }
  html, body { width: 1200px; height: 589px; overflow: hidden; }
  body {
    position: relative;
    background: var(--backdrop);
    font-family: "Source Sans 3", "Helvetica Neue", Arial, sans-serif;
    color: var(--ink);
  }
  .sheet { position: absolute; background: var(--paper); }

  .brand { position: absolute; display: flex; align-items: center; gap: 0.18em; }
  .brand-square { width: 0.55em; height: 0.55em; background: var(--green); }
  .brand-name { font-weight: 600; letter-spacing: 0.02em; color: var(--ink); line-height: 1; }

  .web { position: absolute; font-size: 6px; line-height: 7px; color: var(--ink-soft); white-space: nowrap; }
  .contact { position: absolute; font-size: 5.5px; line-height: 7px; text-transform: uppercase; color: var(--ink-soft); white-space: nowrap; }

  .letterhead-back { left: 40px; top: 42px; width: 353px; height: 506px;
    background: linear-gradient(180deg, var(--slate) 0%, var(--slate-dark) 100%); }
  .letterhead-back .brand { left: 20px; top: 424px; font-size: 42px; }
  .letterhead-back .web { left: 305px; top: 458px; color: #2a2a2a; }

  .letterhead { left: 412px; top: 42px; width: 345px; height: 506px; }
  .letterhead .brand { left: 28px; top: 34px; font-size: 27px; }
  .letterhead .contact { left: 239px; top: 42px; }
  .letter-body { position: absolute; left: 28px; top: 98px; width: 285px;
    font-size: 6.4px; line-height: 8.2px; font-weight: 600; color: var(--ink); }
  .letter-body p { margin-bottom: 8px; }
  .letter-body .gap { margin-bottom: 24px; }
  .letterhead .footer-rule { position: absolute; left: 28px; right: 20px; top: 474px; height: 1px; background: var(--rule); }
  .letterhead .web { left: 285px; top: 465px; }

  .envelope-back { left: 793px; top: 42px; width: 355px; height: 170px; }
  .envelope-back svg { position: absolute; left: 0; top: 0; }
  .envelope-back .brand { left: 136px; top: 18px; font-size: 21px; }

  .envelope-front { left: 795px; top: 250px; width: 353px; height: 166px; }
  .envelope-front .brand { left: 15px; top: 16px; font-size: 23px; }
  .envelope-front .contact { left: 20px; top: 132px; }
  .envelope-front .web { left: 298px; top: 143px; }
  .envelope-front .footer-rule { position: absolute; left: 20px; right: 14px; top: 153px; height: 1px; background: var(--rule); }

  .card-front { left: 796px; top: 452px; width: 182px; height: 96px; }
  .card-front .brand { left: 22px; top: 32px; font-size: 23px; }

  .card-back { left: 996px; top: 452px; width: 144px; height: 96px; }
  .card-back .brand { left: 70px; top: 12px; font-size: 16px; }
  .person-name { position: absolute; left: 12px; top: 56px; font-size: 8px; line-height: 9px; color: var(--ink); white-space: nowrap; }
  .person-role { position: absolute; left: 12px; top: 67px; font-size: 6px; line-height: 7px; font-weight: 700; font-style: italic; color: var(--ink-soft); }
  .card-back .contact { right: 8px; top: 64px; text-align: right; font-size: 4.5px; line-height: 6px; text-transform: none; }
</style>
</head>
<body>

  <section class="sheet letterhead-back" aria-label="Letterhead reverse">
    <div class="brand"><span class="brand-name">PVTRN</span><span class="brand-square"></span></div>
    <span class="web">www.pvtrn.org</span>
  </section>

  <section class="sheet letterhead" aria-label="Letterhead">
    <div class="brand"><span class="brand-name">PVTRN</span><span class="brand-square"></span></div>
    <div class="contact">Sunday Service, 9:30 AM<br>Map &amp; Directions<br>(555) 014-2278</div>
    <div class="letter-body">
      <p>2150, Alder Crest Road<br>Fresno, CA 93650.</p>
      <p>January 29th, 2011</p>
      <p>Mr. Hallbrook<br>President, Hallbrook Learning House<br>518 Orchard Way<br>Portland, OR 97205</p>
      <p>Dear Mr. Hallbrook:</p>
      <p class="gap">In the first paragraph, one needs to give a brief introduction of oneself. One should also give reference to the purpose of the letter in brief.<br>The second paragraph needs to give the details of the letter and its need. This paragraph is mostly longer than the others and plays the main role in the letter. Keep the sentences short and to the point. Avoid using complex words and sentences.</p>
      <p>The third and last paragraph is the conclusion of the letter and can be kept short.</p>
      <p>Sincerely,</p>
      <p>(this is where the signature of the writer will be placed)</p>
      <p>Tessa Marlowe<br>Read more at Letterdesk: http://www.letterdesk.com/articles/professional-letter-format.html</p>
    </div>
    <div class="footer-rule"></div>
    <span class="web">www.pvtrn.org</span>
  </section>

  <section class="sheet envelope-back" aria-label="Envelope reverse">
    <svg width="355" height="170" viewBox="0 0 355 170" aria-hidden="true">
      <polyline points="0,2 177,88 355,2" fill="none" stroke="#c9c9c9" stroke-width="1"/>
    </svg>
    <div class="brand"><span class="brand-name">PVTRN</span><span class="brand-square"></span></div>
  </section>

  <section class="sheet envelope-front" aria-label="Envelope front">
    <div class="brand"><span class="brand-name">PVTRN</span><span class="brand-square"></span></div>
    <div class="contact">Sunday Service, 9:30 AM<br>Map &amp; Directions<br>(555) 014-2278</div>
    <span class="web">www.pvtrn.org</span>
    <div class="footer-rule"></div>
  </section>

  <section class="sheet card-front" aria-label="Business card front">
    <div class="brand"><span class="brand-name">PVTRN</span><span class="brand-square"></span></div>
  </section>

  <section class="sheet card-back" aria-label="Business card back">
    <div class="brand"><span class="brand-name">PVTRN</span><span class="brand-square"></span></div>
    <span class="person-name">Morgan Feltwick</span>
    <span class="person-role">Director</span>
    <div class="contact">2150 Alder Crest Road<br>Fresno, CA 93650<br>(555) 014-2278<br>www.pvtrn.org</div>
  </section>

</body>
</html>
```